Coastal Learner Bureau business cards

Australian company about to start offering its services. We recruit international students to come to study English, vocational education and postgraduate courses in Australia. We help them find the institution and select the right city they want to come to Australia. We are a young, online oriented and supportive agency. Our clients are between 18 and 35 years old, mainly University students, young professionals or people with work experience. We provide much more information that any other agency offer. We administrate a Facebook group with more than 11.000 members that daily ask questions about general information when coming to Australia, while they are here and even after they leave the country

Target Market(s)

International students from South America, Central America and Europe

Industry/Entity Type

Student

Contact Information for Business Card

Tomas Bilbrea
Managing Director
tomas@kelvarin.com.au
www.kelvoria.com.au
+61 491058264
Melbourne, Australia

Font styles to use
Serif
Sans Serif

Colors

Designer to choose colors to be used in the design.

Requirements
Must have
• Horizontal design
• Standard business card size and shape. If font uses green or yellow colours, they will have to match the ones from the logo
Nice to have
• UPDATE: Use the contents of the green image to design one of the card sides. Use our logo in the background of that side as watermark.
• Passport image, or immigration stamps. A picture of the Yarra River (from Melbourne) would be cool as well.
Should not have
• Non-standard business card size and shape
• Not black as the background colour of any sides as we are not a VIP agency or a hight class service. We are orientes to young people and they like colours, pictures, something attractive.
• Vertical design
• NO YELLOW or BLACK AS THE BACKGROUND COLOUR OF ANY SIDE OF THE BIZ CARD

```html
<!DOCTYPE html>
<html lang="en">
<head>
<meta charset="utf-8">
<title>Coastal Learner Bureau – Business Cards</title>
<link href="https://fonts.googleapis.com/css2?family=Roboto:wght@400;500&family=Roboto+Condensed:wght@700&display=swap" rel="stylesheet">
<style>
  :root {
    --green: #165a3a;
    --yellow: #dfb70f;
    --card-white: #f2f2f1;
    --text-grey: #3d3d3d;
    --rule-grey: #8a8a8a;
    --stage: #2b2b2b;
    --white: #ffffff;
  }
  * { margin: 0; padding: 0; box-sizing: border-box; }
  html, body {
    width: 1200px; height: 960px; overflow: hidden;
    background: var(--stage);
    font-family: "Roboto", Arial, sans-serif;
  }
  .canvas { position: relative; width: 1200px; height: 960px; }

  .card { position: absolute; width: 600px; height: 343px; overflow: hidden; }

  /* Front */
  .card-front { left: 314px; top: 113px; background: var(--card-white); }
  .brand-name {
    position: absolute; right: 37px; top: 72px;
    font-family: "Roboto", Arial, sans-serif; font-weight: 500;
    font-size: 52px; line-height: 1; color: var(--green); letter-spacing: 0.5px;
  }
  .holder-name {
    position: absolute; left: 38px; top: 192px;
    font-family: "Roboto Condensed", "Arial Narrow", sans-serif; font-weight: 700;
    font-size: 23px; line-height: 28px; color: var(--green); letter-spacing: 0.2px;
  }
  .holder-title {
    position: absolute; left: 38px; top: 219px;
    font-size: 15.5px; line-height: 18px; font-weight: 500; color: var(--yellow); letter-spacing: 0.3px;
  }
  .divider {
    position: absolute; left: 38px; top: 244px; width: 525px; height: 1px;
    background: var(--rule-grey);
  }
  .contact-list { position: absolute; left: 38px; top: 256px; list-style: none; }
  .contact-item {
    display: flex; align-items: center; gap: 7px;
    font-size: 14.5px; color: var(--text-grey); line-height: 19px;
  }
  .contact-item svg { width: 14px; height: 14px; fill: var(--green); }
  .location {
    position: absolute; right: 37px; top: 273px;
    font-size: 14.5px; line-height: 18px; color: var(--text-grey);
  }
  .band-yellow {
    position: absolute; left: 0; top: 320px; width: 352px; height: 10px;
    background: var(--yellow); border-top-right-radius: 10px;
  }
  .band-green {
    position: absolute; left: 0; top: 330px; width: 600px; height: 13px;
    background: var(--green);
  }
  .web-tab {
    position: absolute; left: 350px; top: 311px; width: 250px; height: 32px;
    background: var(--green); border-top-left-radius: 16px;
    color: var(--white); font-size: 14.5px; line-height: 30px; padding-left: 55px;
  }

  /* Back */
  .card-back { left: 311px; top: 472px; background: var(--green); }
  .back-brand {
    position: absolute; left: 0; top: 136px; width: 600px; text-align: center;
    font-family: "Roboto", Arial, sans-serif; font-weight: 500;
    font-size: 64px; line-height: 1; color: var(--white);
  }
  .tagline-row {
    position: absolute; left: 80px; top: 299px; width: 440px;
    display: flex; align-items: center; gap: 4px;
  }
  .tagline-rule { flex: 1; height: 1px; }
  .tagline-rule.left { background: linear-gradient(to right, rgba(255,255,255,0), #fff); }
  .tagline-rule.right { background: linear-gradient(to left, rgba(255,255,255,0), #fff); }
  .tagline { font-size: 14.5px; color: var(--white); white-space: nowrap; }
</style>
</head>
<body>
<main class="canvas">

  <section class="card card-front" aria-label="Business card front">
    <div class="brand-name">Kelvoria</div>

    <h1 class="holder-name">TOMAS BILBREA</h1>
    <p class="holder-title">MANAGING DIRECTOR</p>
    <div class="divider"></div>

    <ul class="contact-list">
      <li class="contact-item">
        <svg viewBox="0 0 24 24" aria-hidden="true"><path d="M6.6 10.8a15.1 15.1 0 0 0 6.6 6.6l2.2-2.2a1 1 0 0 1 1-.25 11.4 11.4 0 0 0 3.6.57 1 1 0 0 1 1 1V20a1 1 0 0 1-1 1A17 17 0 0 1 3 4a1 1 0 0 1 1-1h3.5a1 1 0 0 1 1 1c0 1.25.2 2.45.57 3.57a1 1 0 0 1-.25 1z"/></svg>
        +61 491058264
      </li>
      <li class="contact-item">
        <svg viewBox="0 0 24 24" aria-hidden="true"><path d="M2 5h20v14H2z M2 5l10 8 10-8" /></svg>
        tomas@kelvarin.com.au
      </li>
    </ul>

    <p class="location">Melbourne, Australia</p>

    <div class="band-yellow"></div>
    <div class="band-green"></div>
    <div class="web-tab">www.kelvoria.com.au</div>
  </section>

  <section class="card card-back" aria-label="Business card back">
    <div class="back-brand">Kelvoria</div>
    <div class="tagline-row">
      <span class="tagline-rule left"></span>
      <span class="tagline">Hacemos más por ti!</span>
      <span class="tagline-rule right"></span>
    </div>
  </section>

</main>
</body>
</html>
```